VELTAR WEBSITE

need to create a new website for VELTAR ltd
the company deals with all aspects of safety products & safety wear
we need a simple website to show
ideas can be taken from following website whose products we shall distribute in kenya
www.kwr.co.uk
www.dorvik.eu
www.brimtoolsupplyco.com
www.gardvalewerks.co.za

we need following tabs
1) home - basic company information
2) products - broken down to following categories ie gloves, head protection, ear protection, mouth protection, foot protection
3) contacts

the company profile is a reputable company dealing with all aspects of safety, HSE (health and safety equipment), and PPE (personal protective equipment)

the website should have the dorvik logo for which we are an authorized distributor.
the dorvi industrial range writeup can be picked from their website
Updates

Dear Designers, i shall be able to choose a final design in 2 weeks, sorry i have not been able to finalise this due to a personal reason

Target Market(s)

the buyers are all types of industry who care for their employees safety

Industry/Entity Type

Industrial

Requirements
Must have
• clean look, fresh look, user freindly
Nice to have
• clear images, quick links etc

```html
<!DOCTYPE html>
<html lang="en">
<head>
<meta charset="utf-8">
<title>Veltar – Safety Products</title>
<link href="https://fonts.googleapis.com/css2?family=Open+Sans:wght@300;400;600;700&display=swap" rel="stylesheet">
<style>
:root{
  --teal:#12384a;
  --teal-light:#1e4e63;
  --orange:#f7a81b;
  --yellow:#f5c200;
  --text:#333;
  --muted:#8a8a8a;
  --line:#e2e2e2;
  --panel:#f7f7f7;
  --footer:#252525;
}
*{box-sizing:border-box;margin:0;padding:0}
html,body{width:1064px;height:1200px;overflow:hidden;background:#fff;font-family:"Open Sans",sans-serif;color:var(--text)}
.page{position:relative;width:1200px;height:1354px;transform:scale(.88667);transform-origin:0 0}
.abs{position:absolute}

/* header */
.brand{left:110px;top:60px;display:flex;align-items:center;gap:10px}
.brand-mark{width:26px;height:26px;background:var(--orange)}
.brand-name{font-size:34px;font-weight:700;color:var(--teal);letter-spacing:1px}
.contact{right:110px;top:46px;text-align:right;color:#777;font-size:17px;line-height:28px}
.contact div{display:flex;align-items:center;justify-content:flex-end;gap:14px}

/* nav */
.nav{left:110px;top:149px;width:980px;height:48px;border-radius:4px;overflow:hidden;
  background:linear-gradient(#1d4a5e,var(--teal));display:flex}
.nav a{display:flex;align-items:center;padding:0 28px;color:#fff;font-size:13px;text-decoration:none;border-right:1px solid #0c2a38;height:100%}
.nav a.active{background:var(--orange);color:var(--teal);font-weight:600;padding:0 18px;width:86px}
.nav .caret{margin-left:8px;border:4px solid transparent;border-top:5px solid #fff;margin-top:5px}
.search{position:absolute;left:679px;top:13px;width:285px;height:24px;background:#fff;border:1px solid #ccc;font-size:10px;color:#999;padding:4px 10px}
.search svg{position:absolute;right:8px;top:6px}

/* hero */
.hero{left:110px;top:213px;width:980px;height:433px;border-radius:6px;overflow:hidden;
  background:
    radial-gradient(ellipse 30% 40% at 90% 62%,#ffd51a 0%,#f2b90e 45%,rgba(230,160,10,0) 100%),
    radial-gradient(ellipse 22% 14% at 62% 88%,#ffc21c 0%,rgba(240,160,20,0) 100%),
    radial-gradient(ellipse 28% 45% at 56% 35%,#c98a3a 0%,#9a6426 50%,rgba(90,60,30,0) 100%),
    radial-gradient(ellipse 20% 30% at 82% 22%,#d49a40 0%,rgba(160,110,50,0) 100%),
    linear-gradient(180deg,rgba(0,0,0,0) 70%,#c9a06a 86%,#b88d58 100%),
    linear-gradient(100deg,#2a2016 0%,#4a3624 35%,#6a4a2a 60%,#8f8a80 100%)}
.hero-shadow{left:130px;top:640px;width:940px;height:30px;background:radial-gradient(ellipse at 50% 0%,rgba(0,0,0,.28),transparent 70%)}
.caption{left:142px;top:366px;width:382px;height:204px;background:rgba(15,12,8,.84);border-top:2px solid #fff;padding:18px 14px 0 17px;color:#fff}
.caption h1{font-size:34px;font-weight:300;color:var(--orange);line-height:40px;margin-bottom:8px;letter-spacing:-.5px}
.caption h1 b{font-weight:600}
.caption p{font-size:14px;line-height:20px;letter-spacing:-.35px}
.pager{left:419px;top:548px;display:flex;gap:6px}
.pager i{width:7px;height:7px;background:#fff}
.pager i.on{background:var(--teal-light)}

/* categories */
.cats{left:110px;top:693px;display:flex;gap:8px}
.cat{width:156px;text-align:center}
.cat .ph{height:143px;border:1px solid #ddd;box-shadow:inset 0 0 0 3px #fff}
.cat span{display:block;margin-top:14px;font-size:13px;line-height:14px;color:#222}
.cat.active span{font-size:14px;font-weight:600;color:var(--teal);text-transform:uppercase}
.ph-head{background:radial-gradient(ellipse 45% 35% at 30% 30%,#f3a01c,rgba(243,160,28,0)),radial-gradient(ellipse 40% 30% at 70% 38%,#f6a624,rgba(246,166,36,0)),radial-gradient(ellipse 50% 25% at 60% 72%,#a9a9a9,rgba(169,169,169,0)),#fdfdfd}
.ph-mouth{background:radial-gradient(ellipse 35% 45% at 45% 45%,#b8aaa6,rgba(184,170,166,0)),linear-gradient(180deg,#f2f0ef 60%,#f3c8c4 100%)}
.ph-ear{background:radial-gradient(ellipse 40% 45% at 50% 50%,#d3d5d7,rgba(211,213,215,0)),#f2f3f4}
.ph-foot{background:radial-gradient(ellipse 45% 30% at 50% 55%,#f1e6da,rgba(241,230,218,0)),#fafafa}
.ph-health{background:radial-gradient(ellipse 30% 30% at 25% 35%,#f4e08c,rgba(244,224,140,0)),radial-gradient(ellipse 40% 30% at 50% 80%,#f4c59a,rgba(244,197,154,0)),linear-gradient(135deg,#ede6dc,#d9d2cc)}
.ph-ppe{background:radial-gradient(ellipse 22% 40% at 30% 65%,#f3c79f,rgba(243,199,159,0)),radial-gradient(ellipse 22% 40% at 68% 70%,#f4c79c,rgba(244,199,156,0)),radial-gradient(ellipse 30% 15% at 50% 10%,#f1b3a8,rgba(241,179,168,0)),#efeeec}
.arrow{top:756px}

/* news */
.news{left:111px;top:926px;width:300px;height:358px;background:var(--panel);border:1px solid var(--line);border-radius:3px;padding:16px 0 0 16px}
.panel-title{font-size:25px;font-weight:300;color:var(--teal)}
.panel-title b{font-weight:400}
.news-dots{position:absolute;right:23px;top:26px;display:flex;gap:5px}
.news-dots i{width:9px;height:9px;border-radius:50%;background:var(--yellow)}
.news-dots i:first-child{background:var(--teal)}
.rule{border-top:1px dashed #ccc}
.news .rule{width:257px;margin-top:10px}
.news-item{display:flex;gap:7px;margin-top:15px}
.news-item + .news-item{margin-top:21px}
.news-item .ph{width:80px;height:72px;flex:none;background:linear-gradient(135deg,#e9e4df,#c4ab98 60%,#8f7767)}
.news-item h3{font-size:15px;font-weight:400;color:#222;line-height:18px}
.news-item p{font-size:12px;color:#9a9a9a;line-height:15px;margin-top:2px;width:165px;letter-spacing:.15px}

/* about */
.about{left:435px;top:926px;width:649px;height:356px;background:#fff;border:4px solid #eee;padding:18px 30px 0 34px}
.about .panel-title{font-size:26px;font-weight:300;padding-left:2px}
.about .rule{margin-top:14px;width:580px}
.about p{font-size:14px;font-weight:300;color:#555;line-height:20px;margin-top:18px;width:590px;padding-left:2px;letter-spacing:-.3px}
.about p + p{margin-top:20px}
.btn{display:inline-block;margin-top:16px;margin-left:3px;background:var(--teal);color:#fff;font-size:14px;padding:7px 23px;border-radius:2px}

/* footer */
.footer{left:0;top:1300px;width:1200px;height:54px;background:var(--footer);color:#ccc;font-size:13px;text-align:center;line-height:56px}
</style>
</head>
<body>
<div class="page">
  <div class="abs brand"><span class="brand-mark"></span><span class="brand-name">VELTAR</span></div>

  <div class="abs contact">
    <div><svg width="16" height="11" viewBox="0 0 16 11"><rect x=".5" y=".5" width="15" height="10" fill="#bbb"/><path d="M.5 .5 8 6l7.5-5.5" stroke="#fff" fill="none"/></svg>www.veltarsafety.com</div>
    <div><svg width="16" height="16" viewBox="0 0 16 16"><path d="M3 1l3 3-2 2c1 2 3 4 5 5l2-2 3 3-2 3C7 14 2 9 1 3z" fill="#aaa"/></svg>090-555-0142-310</div>
  </div>

  <nav class="abs nav">
    <a class="active">HOME</a>
    <a>PRODUCTS<span class="caret"></span></a>
    <a>CONTACTS</a>
    <div class="search">enter search terms
      <svg width="10" height="10" viewBox="0 0 10 10"><circle cx="4" cy="4" r="3" stroke="#aaa" fill="none"/><path d="M6.2 6.2 9.5 9.5" stroke="#aaa"/></svg>
    </div>
  </nav>

  <div class="abs hero" role="img" aria-label="Photo of leather work boots, a yellow hard hat, amber safety glasses and work gloves on a wooden floor"></div>
  <div class="abs hero-shadow"></div>
  <div class="abs caption">
    <h1><b>Veltar</b> Protection</h1>
    <p>It is a long established fact that a reader will be distracted by the readable content of a page when looking at its layout. The point of using Lorem Ipsum is that it has a more-or-less normal distribution of letters, as opposed to using 'Content here, content here',</p>
  </div>
  <div class="abs pager"><i></i><i></i><i></i><i></i><i class="on"></i><i></i></div>

  <svg class="abs arrow" style="left:86px" width="16" height="20" viewBox="0 0 16 20"><path d="M12 2 4 10l8 8" stroke="#ccc" stroke-width="4" fill="none"/></svg>
  <svg class="abs arrow" style="left:1096px" width="16" height="20" viewBox="0 0 16 20"><path d="M4 2l8 8-8 8" stroke="#ccc" stroke-width="4" fill="none"/></svg>

  <div class="abs cats">
    <div class="cat active"><div class="ph ph-head" role="img" aria-label="Photo of orange hard hats resting on grey work gloves"></div><span>Head Protection</span></div>
    <div class="cat"><div class="ph ph-mouth" role="img" aria-label="Photo of a cyclist wearing a dust mask"></div><span>Mouth Protection</span></div>
    <div class="cat"><div class="ph ph-ear" role="img" aria-label="Photo of grey ear defenders"></div><span>Ear Protection</span></div>
    <div class="cat"><div class="ph ph-foot" role="img" aria-label="Photo of protective footwear"></div><span>Foot Protection</span></div>
    <div class="cat"><div class="ph ph-health" role="img" aria-label="Photo of assorted safety equipment and gloves"></div><span>Health and safety equipment</span></div>
    <div class="cat"><div class="ph ph-ppe" role="img" aria-label="Photo of workers in hard hats and hi-vis vests"></div><span>Personal protective equipment</span></div>
  </div>

  <section class="abs news">
    <h2 class="panel-title">Our <b>News</b></h2>
    <div class="news-dots"><i></i><i></i><i></i><i></i></div>
    <div class="rule"></div>
    <div class="news-item"><div class="ph" role="img" aria-label="Portrait photo of a news author"></div><div><h3>Lorem Lipsum</h3><p>It is a long established fact that a reader will be distracted by the readable</p></div></div>
    <div class="news-item"><div class="ph" role="img" aria-label="Portrait photo of a news author"></div><div><h3>Lorem Lipsum</h3><p>It is a long established fact that a reader will be distracted by the readable</p></div></div>
    <div class="news-item"><div class="ph" role="img" aria-label="Portrait photo of a news author"></div><div><h3>Lorem Lipsum</h3><p>It is a long established fact that a reader will be distracted by the readable</p></div></div>
  </section>

  <section class="abs about">
    <h2 class="panel-title">About Us</h2>
    <div class="rule"></div>
    <p>It is a long established fact that a reader will be distracted by the readable content of a page when looking at its layout. The point of using Lorem Ipsum is that it has a more-or-less normal distribution of letters, as opposed to using 'Content here, content here', making it look like readable English. Many desktop publishing packages and web page editors now use Lorem Ipsum as their default model text, and a search for 'lorem ipsum' will uncover many web sites still in their infancy. Various versions have evolved over the years, sometimes by accident, sometimes on purpose (injected humour and the like).</p>
    <p>It is a long established fact that a reader will be distracted by the readable content of a page when looking at its layout.</p>
    <span class="btn">Read More</span>
  </section>

  <footer class="abs footer">©2003 Veltar Protection, Inc. | &nbsp; All rights reserved.</footer>
</div>
</body>
</html>
```